I would like a business card to match my truck wrap and logo. I would like the font to match my existing business card please.

Industry/Entity Type

Painter

Contact Information for Business Card

Rodrigo Fenwar 801-437-2190 Fenwarcoatings.utah@brelmox.com
SERVICES - Custom Paint & Stain, Interior & Exterior, Epoxy Coatings / Garage Floors, Cabinet Refinishing, Log Staining and Refinishing.

Requirements
Nice to have
• I would like to have the white and grey line like the bottom of my vehicle wrap, Light Grey to match my truck also.

```html
<!DOCTYPE html>
<html lang="en">
<head>
<meta charset="utf-8">
<title>Fenwar Painting — Business Card</title>
<link rel="stylesheet" href="https://fonts.googleapis.com/css2?family=Montserrat:wght@400;500;600;700&display=swap">
<style>
  :root {
    --canvas: #161616;
    --card: #1f1f20;
    --card-edge: #262627;
    --accent: #12a9e6;
    --ink: #f2f2f2;
    --muted: #d8d8d8;
  }
  * { margin: 0; padding: 0; box-sizing: border-box; }
  html, body {
    width: 1200px; height: 900px; overflow: hidden;
    background: var(--canvas);
    font-family: "Montserrat", sans-serif;
  }
  .stage {
    width: 1200px; height: 900px;
    display: flex; flex-direction: column; align-items: center; justify-content: center;
    gap: 40px;
  }
  .card {
    position: relative;
    width: 660px; height: 377px;
    overflow: hidden;
    background: linear-gradient(135deg, var(--card-edge), var(--card) 60%);
    box-shadow: 0 12px 30px rgba(0,0,0,.55);
    color: var(--ink);
  }
  .card::after {
    content: ""; position: absolute; left: 0; right: 0; bottom: 0;
    height: 5px; background: var(--accent);
  }

  .brand { display: flex; align-items: center; gap: 14px; }
  .brand-mark { width: 40px; height: 40px; background: var(--accent); flex: none; }
  .brand-name {
    font-weight: 700; color: var(--accent);
    line-height: 1.05; letter-spacing: 1px; text-transform: uppercase;
  }
  .brand-name span { display: block; letter-spacing: 9px; font-size: .42em; }

  /* front */
  .card-front .brand { position: absolute; left: 50%; top: 92px; transform: translateX(-50%); }
  .card-front .brand-name { font-size: 46px; color: var(--muted); }
  .services { position: absolute; left: 0; right: 0; top: 238px; text-align: center; }
  .services-title { color: var(--accent); font-weight: 500; font-size: 17px; letter-spacing: 1.5px; margin-bottom: 4px; }
  .services-list { font-size: 14.5px; line-height: 1.5; color: var(--ink); }
  .sep { color: var(--accent); padding: 0 4px; }

  /* back */
  .card-back .brand { position: absolute; left: 44px; top: 150px; }
  .card-back .brand-name { font-size: 40px; }
  .divider { position: absolute; left: 326px; top: 108px; width: 2px; height: 150px; background: var(--accent); }
  .contact { position: absolute; left: 350px; top: 112px; width: 290px; }
  .person-name { color: var(--accent); font-weight: 600; font-size: 24px; letter-spacing: 1px; text-transform: uppercase; white-space: nowrap; }
  .person-role { font-size: 15px; margin: 2px 0 16px; }
  .contact-line { display: flex; align-items: center; gap: 8px; font-size: 14px; margin-bottom: 7px; white-space: nowrap; }
  .contact-line svg { width: 12px; height: 12px; flex: none; }
</style>
</head>
<body>
<main class="stage">
  <section class="card card-front">
    <div class="brand">
      <div class="brand-mark"></div>
      <div class="brand-name">Fenwar<span>Painting</span></div>
    </div>
    <div class="services">
      <p class="services-title">SERVICES</p>
      <p class="services-list">Custom Paint &amp; Stain<span class="sep">|</span>Interior &amp; Exterior<span class="sep">|</span>Epoxy Coatings / Garage Floors</p>
      <p class="services-list">Cabinet Refinishing<span class="sep">|</span>Log Staining and Refinishing.</p>
    </div>
  </section>

  <section class="card card-back">
    <div class="brand">
      <div class="brand-mark"></div>
      <div class="brand-name">Fenwar<span>Painting</span></div>
    </div>
    <div class="divider"></div>
    <div class="contact">
      <p class="person-name">Rodrigo Fenwar</p>
      <p class="person-role">Director</p>
      <p class="contact-line">
        <svg viewBox="0 0 12 12" aria-hidden="true"><path d="M3 1 L5 3.5 L4 5 Q5 7 7 8 L8.5 7 L11 9 L9.5 11 Q2 10 1 2.5 Z" fill="var(--accent)"/></svg>
        801-437-2190
      </p>
      <p class="contact-line">
        <svg viewBox="0 0 12 12" aria-hidden="true"><rect x="1" y="2.5" width="10" height="7" fill="none" stroke="var(--accent)" stroke-width="1.2"/><path d="M1 3 L6 7 L11 3" fill="none" stroke="var(--accent)" stroke-width="1.2"/></svg>
        Fenwarcoatings.utah@brelmox.com
      </p>
      <p class="contact-line">
        <svg viewBox="0 0 12 12" aria-hidden="true"><circle cx="6" cy="6" r="5" fill="none" stroke="var(--accent)" stroke-width="1.1"/><ellipse cx="6" cy="6" rx="2.2" ry="5" fill="none" stroke="var(--accent)" stroke-width="1"/><path d="M1 6 H11" stroke="var(--accent)" stroke-width="1"/></svg>
        www.fenwarpainting.utah.com
      </p>
    </div>
  </section>
</main>
</body>
</html>
```